Healthy Food Healthy Brain Rack Card

We want a new 2 page (front and page) 3.67" x 8.5" rack card. This rack card is the first of a series we are creating. We will have five more eventually.

The minimum font size for the text on the front is 11 point and also for other main body text.

Use the text on the word document.

The images and layout in the word document are just sample ideas we had.

We have a subscripton to plivora pics images so prefer to get images from there or free high quality images.

The document is for older readers. Do not put text over graphics and keep it simple and easy to read with high contrast.

We are open to any color scheme, though something that conveys fresh and healthy, is good.

We want some very simple design element(s) incorporated that convey Native American communities or heritage. But NO head dress, teepee graphics, etc.

At the top, of the first page we would like a collage of healthy food images. This can include fish, chicken, fresh vegetables, berries, brown rice, etc.

On the back side, the text below the brown box on the word document with the title "mock up" can be smaller as needed.

Please remember to include the funding statement - it can be in a very small font 6/7 point.

For more information about our project, please visit https://veltronaq.org/mind-care/

```html
<!DOCTYPE html>
<html lang="en">
<head>
<meta charset="utf-8">
<title>Healthy Food Healthy Brain – Rack Card</title>
<link href="https://fonts.googleapis.com/css2?family=Fira+Sans:ital,wght@0,400;0,500;0,600;1,600;1,700&family=Montserrat:wght@800&display=swap" rel="stylesheet">
<style>
  :root{
    --canvas:#f3f3f3;
    --paper:#ffffff;
    --berry:#981b2e;
    --ink:#1e1e1e;
    --teal:#5ca7b2;
    --muted:#6a6a6a;
    --veg-green:#d9e6c4;
    --veg-purple:#e6d3ea;
    --veg-orange:#f7dcc0;
  }
  *{box-sizing:border-box;margin:0;padding:0}
  html,body{width:1200px;height:1200px;overflow:hidden;background:var(--canvas)}
  body{position:relative;font-family:"Fira Sans",sans-serif;color:var(--ink)}
  .card{position:absolute;top:67px;width:467px;height:1082px;background:var(--paper);overflow:hidden;box-shadow:0 1px 4px rgba(0,0,0,.12)}
  .card--front{left:109px}
  .card--back{left:600px}
  .band{position:absolute;left:0;width:100%}
  .band--berry{background:var(--berry);color:#fff}

  /* Front */
  .front-art{position:absolute;left:0;top:0;width:100%;height:360px;
    background:radial-gradient(ellipse at 50% 55%,rgba(255,255,255,1) 0 38%,rgba(255,255,255,0) 62%),
    linear-gradient(135deg,var(--veg-orange),var(--veg-green) 45%,var(--veg-purple))}
  .front-title{position:absolute;top:82px;left:0;width:100%;text-align:center;font-family:"Montserrat",sans-serif;font-weight:800;font-size:51px;line-height:52px;color:var(--berry);letter-spacing:.5px}
  .front-intro{position:absolute;top:303px;left:30px;right:30px;text-align:center;font-style:italic;font-weight:600;font-size:18.6px;line-height:24.8px;color:var(--berry)}
  .steps{top:452px;height:452px;padding:26px 30px 0 30px}
  .steps__heading{font-weight:600;font-size:17px;margin-bottom:17px}
  .steps__list{list-style:none;font-size:17.6px;line-height:28.3px}
  .steps__list li{position:relative;padding-left:14px}
  .steps__list li::before{content:"•";position:absolute;left:0}
  .steps__close{font-weight:600;font-size:17.6px;line-height:28px;margin-top:12px}
  .doctor-note{position:absolute;top:904px;left:0;width:100%;height:74px;display:flex;align-items:center;justify-content:center;text-align:center;font-weight:500;font-size:18px;line-height:25px;text-transform:uppercase}
  .quote{top:978px;height:104px;display:flex;flex-direction:column;justify-content:center;text-align:center;font-style:italic;font-weight:700;font-size:18.2px;line-height:25px}

  /* Back */
  .back-header{top:0;height:99px;display:flex;align-items:center;justify-content:center;font-weight:600;font-size:43px}
  .recipe-photo{position:absolute;left:35px;top:122px;width:177px;height:181px;background:linear-gradient(135deg,#d6d8dc,#f0a488 55%,#9cc27a)}
  .recipe-caption{position:absolute;left:35px;top:303px;width:177px;height:57px;background:var(--berry);color:#fff;font-weight:600;font-size:17px;line-height:21px;display:flex;align-items:center;justify-content:center;text-align:center}
  .ingredients{position:absolute;left:224px;top:122px;font-size:17px;line-height:22.1px}
  .ingredients h3{font-size:17px;font-weight:600}
  .ingredients ul{list-style:none}
  .method{top:377px;height:216px;padding:0 16px;display:flex;align-items:center;text-align:center;font-size:16.6px;line-height:22.8px}
  .community{position:absolute;top:610px;left:20px;right:20px;text-align:center;font-style:italic;font-weight:700;font-size:21.8px;line-height:28.4px;color:var(--berry)}
  .back-art{position:absolute;left:0;top:750px;width:100%;height:252px;
    background:radial-gradient(ellipse at 50% 40%,rgba(255,255,255,1) 0 45%,rgba(255,255,255,0) 75%),
    linear-gradient(90deg,var(--veg-green),#fff 40%,#fff 60%,var(--veg-orange))}
  .links{position:absolute;top:782px;left:17px;right:19px;display:flex;justify-content:space-between;font-size:12px;line-height:14.5px}
  .links h4{font-size:16px;font-weight:500;margin-bottom:7px}
  .links .label{font-weight:500}
  .links__brain{text-align:right}
  .program{position:absolute;top:876px;left:0;width:100%;text-align:center;font-size:12px;line-height:14px;color:var(--muted)}
  .program b{font-weight:500}
  .brand{position:absolute;top:920px;left:0;width:100%;display:flex;align-items:center;justify-content:center;gap:12px}
  .brand__dot{width:70px;height:70px;border-radius:50%;background:var(--teal)}
  .brand__name{font-weight:600;font-size:18px;line-height:20px;color:var(--teal);text-transform:uppercase}
  .funding{top:1002px;height:80px;background:var(--teal);color:#fff;font-size:9.2px;line-height:14px;padding:12px 17px 0}
</style>
</head>
<body>

<section class="card card--front">
  <div class="front-art" role="img" aria-label="Hand-drawn collage of garlic, carrot, cherries, mushrooms, beet and radish around the title"></div>
  <h1 class="front-title">HEALTHY<br>FOOD<br>HEALTHY<br>BRAIN</h1>
  <p class="front-intro">Everyone slows down as they get older, both in body and mind. Eating healthier food can help your overall health, including brain health. It may also reduce your risk for memory loss and problems thinking.</p>

  <div class="band band--berry steps">
    <h2 class="steps__heading">Healthier steps to protect your brain:</h2>
    <ul class="steps__list">
      <li>Eat more vegetables, fruits, whole grains, and lower-fat milk</li>
      <li>Use less salt and added sugar</li>
      <li>Eat more fish, chicken, turkey, beans, and nuts</li>
      <li>Cut down on bad fats (“saturated” and trans), cholesterol, and red meat</li>
      <li>Buy fresh, not packaged food when you can</li>
      <li>Limit how much alcohol you drink</li>
      <li>Learn your daily calorie needs for your body size</li>
      <li>Take care of your mental and spiritual health to support your physical and brain health</li>
    </ul>
    <p class="steps__close">Small changes can make a big difference for better brain health.</p>
  </div>

  <p class="doctor-note">Talk to your doctor about more steps<br>to healthier food choices.</p>

  <blockquote class="band band--berry quote">
    <p>“Without the elk, salmon, huckleberries,<br>shellfish, and cedar trees we are nobody…”</p>
    <p>Marla Tenaya (Cedar River)</p>
  </blockquote>
</section>

<section class="card card--back">
  <h2 class="band band--berry back-header">Make This at Home</h2>

  <div class="recipe-photo" role="img" aria-label="Photo of salmon fillet with asparagus, peppers, onion and lemon in an open foil packet"></div>
  <p class="recipe-caption">Grilled Salmon and<br>Veggie Foil Packets</p>

  <div class="ingredients">
    <h3>Ingredients:</h3>
    <ul>
      <li>Salmon</li>
      <li>Asparagus</li>
      <li>Red or Green Peppers</li>
      <li>(Or any seasonal vegetable)</li>
      <li>Onion</li>
      <li>Lemon – sliced</li>
      <li>Basil</li>
      <li>Olive Oil</li>
      <li>Salt and Pepper</li>
      <li>Garlic Powder</li>
    </ul>
  </div>

  <p class="band band--berry method">Cut asparagus, peppers, and onion into bite-size pieces. Cut salmon into 4-6 oz pieces. Tear tin foil large enough to wrap around salmon &amp; veggies (2 layers). Add veggies and salmon to foil. Drizzle with olive oil, season with salt, pepper, basil, garlic &amp; top with a piece of sliced lemon. Wrap foil tightly around food. Grill at 400 degrees for about 20 minutes. Careful opening!</p>

  <p class="community">Food &amp; drink are a source of strength and connection to community. A return to traditional food pathways and eating local, seasonal fresh foods make healthier eating easier.</p>

  <div class="back-art" role="img" aria-label="Soft hand-drawn vegetables framing the resource section: bok choy, radish and carrot"></div>

  <div class="links">
    <div class="links__info">
      <h4>For More Information</h4>
      <p class="label">About Healthier Eating</p>
      <p class="label" style="margin-top:6px">PlateWise Guide</p>
      <p>https://www.platewiseguide.org</p>
    </div>
    <div class="links__brain">
      <h4>About Brain Health</h4>
      <p class="label">Cedar Circle Resource Center<br>for Brain Health</p>
      <p>https://www.cedarcirclebrain.org</p>
    </div>
  </div>

  <p class="program"><b>Northfield Memory Care Program</b><br>https://www.northfieldmemory.org/aging</p>

  <div class="brand">
    <span class="brand__dot"></span>
    <span class="brand__name">Cedar Circle<br>Resource Center<br>for Brain Health</span>
  </div>

  <p class="band funding">This product is supported by the Meridian Health Foundation (MHF) as part of a financial assistance award totaling $348,711 with 100 percent funded by MHF. The contents are those of the author(s) and do not necessarily represent the official views of, nor an endorsement, by MHF.</p>
</section>

</body>
</html>
```